Medical Billing Company Needs a Business Card Design

We need a business card design for a Florida based medical billing company called 'Clinicians Keystone Solutions'. We specialize in providing revenue cycle management services to physician and therapist offices (we're basically their back-office processing partner for providing billing software, claims submissions, A/R follow-up and patient statements & collections. Our logo is red and blue-ish, so make sure that whatever other elements are used will match appropriately. Our current business card design has a too small font size. I'd like to project an image that shows we are modern & reliable. On a side note, I'm planning on using ZUB for printing these cards.

Target Market(s)

Office managers, physicians, therapists

Industry/Entity Type

Printing

Requirements
Must have
• Logo
Name of Employee
Phone
Fax
E-mail
Website

```html
<!DOCTYPE html>
<html lang="en">
<head>
<meta charset="utf-8">
<title>Clinicians Keystone Solutions – Business Card</title>
<link href="https://fonts.googleapis.com/css2?family=Lato:wght@400;700&display=swap" rel="stylesheet">
<style>
  :root {
    --backdrop: #ecebe8;
    --silver-light: #f4f5f6;
    --silver-mid: #dcdee0;
    --silver-dark: #c9cbce;
    --navy: #262470;
    --brand-red: #b8323a;
    --ink-grey: #5a5c60;
    --white: #ffffff;
    --shadow: rgba(0, 0, 0, 0.18);
  }
  * { box-sizing: border-box; margin: 0; padding: 0; }
  html, body {
    width: 1200px;
    height: 720px;
    overflow: hidden;
    background: var(--backdrop);
    font-family: "Lato", sans-serif;
  }
  .stage {
    position: relative;
    width: 1200px;
    height: 720px;
    display: flex;
    align-items: center;
    justify-content: center;
    gap: 40px;
  }
  .card {
    position: relative;
    width: 520px;
    height: 297px;
    border-radius: 4px;
    overflow: hidden;
    background: linear-gradient(160deg, var(--silver-mid) 0%, var(--silver-light) 35%, var(--silver-dark) 60%, var(--silver-light) 100%);
    box-shadow: 0 8px 24px var(--shadow);
  }
  .wordmark {
    position: absolute;
    left: 0;
    right: 0;
    text-align: center;
    font-weight: 400;
    color: var(--navy);
    letter-spacing: 0.14em;
    white-space: nowrap;
  }
  /* Contact side */
  .card--contact .wordmark { top: 46px; font-size: 25px; }
  .address {
    position: absolute;
    top: 112px;
    left: 0;
    right: 0;
    text-align: center;
    font-size: 13px;
    letter-spacing: 0.08em;
    color: var(--ink-grey);
  }
  .info-band {
    position: absolute;
    left: 0;
    right: 0;
    bottom: 0;
    height: 148px;
    background: var(--navy);
    color: var(--white);
    padding: 18px 28px;
  }
  .band-accent {
    position: absolute;
    right: 40px;
    top: 22px;
    width: 46px;
    height: 46px;
    border: 1.5px solid rgba(255, 255, 255, 0.22);
    border-radius: 4px;
  }
  .employee-name { font-size: 19px; font-weight: 400; }
  .employee-title { font-size: 14px; }
  .contact-list { list-style: none; margin-top: 8px; }
  .contact-list li {
    display: flex;
    align-items: center;
    gap: 8px;
    font-size: 14px;
    line-height: 21px;
  }
  .contact-list svg { width: 12px; height: 12px; flex: none; }
  /* Brand side */
  .card--brand .wordmark { top: 118px; font-size: 30px; }
  .card--brand .web-address {
    position: absolute;
    right: 34px;
    bottom: 46px;
    font-size: 16px;
    letter-spacing: 0.08em;
    color: var(--ink-grey);
  }
</style>
</head>
<body>
<main class="stage">
  <section class="card card--contact" aria-label="Business card, contact side">
    <div class="wordmark">CLINICIANS KEYSTONE</div>
    <p class="address">Street Name, City Name, State Zip Code</p>
    <div class="info-band">
      <span class="band-accent" aria-hidden="true"></span>
      <p class="employee-name">Your Name, <span class="employee-title">Title</span></p>
      <ul class="contact-list">
        <li>
          <svg viewBox="0 0 12 12" aria-label="Phone"><circle cx="6" cy="6" r="5.3" fill="none" stroke="currentColor" stroke-width="1.2"/><path d="M4 3.5 L5 3.3 L5.4 4.8 L4.8 5.3 Q5.4 6.7 6.7 7.2 L7.2 6.6 L8.7 7 L8.5 8 Q5 8.6 4 3.5Z" fill="currentColor"/></svg>
          123-456-0789
        </li>
        <li>
          <svg viewBox="0 0 12 12" aria-label="Fax"><rect x="1.5" y="4" width="9" height="6" rx="1" fill="none" stroke="currentColor" stroke-width="1.2"/><rect x="3.5" y="1.5" width="5" height="3" fill="none" stroke="currentColor" stroke-width="1"/><line x1="3.5" y1="7.5" x2="8.5" y2="7.5" stroke="currentColor" stroke-width="1"/></svg>
          123-456-0789
        </li>
        <li>
          <svg viewBox="0 0 12 12" aria-label="Email"><rect x="1" y="2.5" width="10" height="7" rx="1" fill="none" stroke="currentColor" stroke-width="1.2"/><path d="M1.5 3 L6 6.5 L10.5 3" fill="none" stroke="currentColor" stroke-width="1.1"/></svg>
          info@clinicianskeystone.com
        </li>
        <li>
          <svg viewBox="0 0 12 12" aria-label="Website"><circle cx="6" cy="6" r="5" fill="none" stroke="currentColor" stroke-width="1.1"/><ellipse cx="6" cy="6" rx="2.2" ry="5" fill="none" stroke="currentColor" stroke-width="0.9"/><line x1="1" y1="6" x2="11" y2="6" stroke="currentColor" stroke-width="0.9"/></svg>
          www.clinicianskeystone.com
        </li>
      </ul>
    </div>
  </section>

  <section class="card card--brand" aria-label="Business card, brand side">
    <div class="wordmark">CLINICIANS KEYSTONE</div>
    <p class="web-address">www.clinicianskeystone.com</p>
  </section>
</main>
</body>
</html>
```